4 page brochure for Logistics Company

Need a 4 page brochure (ie folded A3) for a Logistics company.
Service is a virtual network of warehouse and logistics companies.
Style is professional but accessible.
We have logo and styles designed and will upload these.
We have identified example images that could be used in the brochure.
Content will be uploaded also.
Reason: A couple of designers requested more time
Am giving another 24 hours to finalise and will then select most suitable design
Target Market(s)
40 to 60 year old business owners (traditional) - Australian
Industry/Entity Type
It Company
Requirements
Must have
- Professional
Should not have
- Nothing tacky

```html
<!DOCTYPE html>
<html lang="en">
<head>
<meta charset="utf-8">
<title>Southern Linked Logistics – Brochure Spread</title>
<link rel="stylesheet" href="https://fonts.googleapis.com/css2?family=Open+Sans:ital,wght@0,400;0,600;0,700;1,400&display=swap">
<style>
  :root {
    --bg: #dcdcdc;
    --paper: #ffffff;
    --blue: #1f78c1;
    --blue-deep: #0f4f94;
    --blue-light: #3a95d6;
    --ink: #4a4f55;
    --ink-soft: #6b7178;
    --panel: #eeeff1;
    --band: #7c8b97;
    --band-edge: #6b7a86;
    --photo-dark: #0c2a55;
    --photo-mid: #2d6bb0;
  }
  * { box-sizing: border-box; margin: 0; padding: 0; }
  html, body { width: 1200px; height: 863px; overflow: hidden; }
  body {
    background: radial-gradient(ellipse at 50% 40%, #f2f2f2, var(--bg));
    font-family: "Open Sans", Arial, sans-serif;
    color: var(--ink);
    position: relative;
  }
  .spread {
    position: absolute; left: 34px; top: 32px;
    width: 1132px; height: 800px;
    display: flex;
    box-shadow: 0 10px 30px rgba(0,0,0,.18);
  }
  .page { position: relative; width: 566px; height: 800px; background: var(--paper); overflow: hidden; }
  .page--left { border-right: 1px solid #e2e4e7; }

  /* Left page header */
  .header-band { position: absolute; left: 0; top: 0; width: 566px; height: 200px; }
  .page-title {
    position: absolute; left: 26px; top: 22px;
    font-size: 26px; font-weight: 400; color: #fff; letter-spacing: .2px;
  }
  .header-intro {
    position: absolute; left: 26px; top: 66px; width: 370px;
    font-size: 10px; line-height: 1.4; font-weight: 600; color: #fff;
  }
  .section-heading {
    position: absolute; font-size: 13px; font-weight: 400;
    color: var(--blue); text-transform: uppercase; letter-spacing: .2px;
  }
  .tick-list { list-style: none; }
  .tick-list li {
    position: relative; padding-left: 18px; margin-bottom: 7px;
    font-size: 9.5px; line-height: 1.3; color: var(--ink);
  }
  .tick-list li svg { position: absolute; left: 0; top: 1px; width: 11px; height: 11px; }
  .dynamics-list { position: absolute; left: 26px; top: 190px; width: 260px; }
  .profit-chart { position: absolute; left: 316px; top: 180px; width: 230px; height: 130px; }

  /* Exit rows */
  .exit-row { position: absolute; left: 0; width: 566px; }
  .exit-row__panel { position: absolute; left: 200px; right: 0; top: 0; bottom: 0; background: var(--panel); }
  .exit-row__label {
    position: absolute; left: 0; top: 0; height: 44px; width: 220px;
    background: linear-gradient(90deg, var(--blue-deep), var(--blue));
    clip-path: polygon(0 0, 92% 0, 100% 50%, 92% 100%, 0 100%);
    color: #fff; font-size: 10px; line-height: 1.35; padding: 6px 26px;
  }
  .exit-row__label strong { font-weight: 700; }
  .exit-row .tick-list { position: absolute; left: 232px; top: 8px; width: 310px; }
  .exit-row .tick-list li { font-size: 8.5px; color: var(--ink-soft); margin-bottom: 8px; }

  /* Right page */
  .hero-photo { position: absolute; left: 0; top: 0; width: 566px; height: 260px; }
  .solution-title {
    position: absolute; left: 34px; top: 256px;
    font-size: 27px; font-weight: 400; line-height: 1.15; color: var(--blue);
  }
  .solution-intro {
    position: absolute; left: 34px; top: 338px; width: 330px;
    font-size: 9.5px; line-height: 1.45; font-style: italic; color: var(--ink-soft);
  }
  .benefit-heading { left: 34px; top: 418px; width: 500px; line-height: 1.3; font-size: 14px; }
  .benefits { position: absolute; left: 0; top: 470px; width: 566px; }
  .benefit { position: relative; height: 70px; margin-bottom: 6px; }
  .benefit__band {
    position: absolute; left: 64px; right: 22px; top: 0; bottom: 0;
    background: linear-gradient(180deg, var(--band), var(--band-edge));
    clip-path: polygon(0 0, 100% 0, 97% 100%, 0 100%);
  }
  .benefit__badge {
    position: absolute; left: 30px; top: 10px; width: 54px; height: 54px; border-radius: 50%;
    background: var(--blue); border: 2px solid #fff; color: #fff;
    font-size: 10.5px; line-height: 1.15; text-align: center;
    display: flex; align-items: center; justify-content: center;
    box-shadow: 0 2px 4px rgba(0,0,0,.2);
  }
  .benefit .tick-list { position: absolute; left: 96px; top: 9px; width: 420px; }
  .benefit .tick-list li { color: #fff; font-size: 8.6px; margin-bottom: 4px; }
</style>
</head>
<body>
<svg width="0" height="0" style="position:absolute">
  <defs>
    <symbol id="tick" viewBox="0 0 12 12">
      <circle cx="6" cy="6" r="5" fill="none" stroke="currentColor" stroke-width="1.4"/>
      <path d="M3.4 6.2 L5.3 8 L8.8 4.2" fill="none" stroke="currentColor" stroke-width="1.5"/>
    </symbol>
  </defs>
</svg>

<main class="spread">
  <!-- Left page: the challenges -->
  <section class="page page--left">
    <svg class="header-band" viewBox="0 0 566 200" aria-hidden="true">
      <defs>
        <linearGradient id="bandGrad" x1="0" y1="0" x2="1" y2="0">
          <stop offset="0" stop-color="#0f4f94"/>
          <stop offset="1" stop-color="#3a95d6"/>
        </linearGradient>
      </defs>
      <path d="M0 0 H566 V40 C480 110 420 120 360 130 L0 145 Z" fill="url(#bandGrad)"/>
    </svg>
    <h1 class="page-title">The challenges (Why?)</h1>
    <p class="header-intro">Australian warehouse business owners are facing unprecedented challenges to diversify their client base, compete for work with national clients, enhance their profitability and ultimately, exit their business.</p>

    <h2 class="section-heading" style="left:26px; top:164px;">Australian warehouse industry dynamics</h2>
    <ul class="tick-list dynamics-list" style="color:var(--blue)">
      <li><svg><use href="#tick"/></svg>Exceptionally fragmented – 1,600 businesses across Australia</li>
      <li><svg><use href="#tick"/></svg>Single site operators – increasing challenge to compete against corporates to secure larger contracts</li>
      <li><svg><use href="#tick"/></svg>Accelerating industry consolidation</li>
      <li><svg><use href="#tick"/></svg>Substantial margin pressure – Gross Profits falling 3% FY13 to FY15</li>
      <li><svg><use href="#tick"/></svg>High customer concentration risk</li>
      <li><svg><use href="#tick"/></svg>Ongoing need to invest in technology to maintain market share</li>
    </ul>

    <svg class="profit-chart" viewBox="0 0 230 130" role="img" aria-label="Area chart of gross profit falling from about 42% in FY13 to about 39% in FY15">
      <rect x="0.5" y="0.5" width="229" height="129" fill="#fff" stroke="#c9cdd2"/>
      <text x="120" y="16" font-size="8" text-anchor="middle" fill="#333" font-family="Open Sans, sans-serif">Gross Profit (approx)</text>
      <g font-size="5.5" fill="#555" font-family="Open Sans, sans-serif" text-anchor="end">
        <text x="30" y="10">42.00%</text><text x="30" y="22">41.50%</text><text x="30" y="34">41.00%</text>
        <text x="30" y="46">40.50%</text><text x="30" y="58">40.00%</text><text x="30" y="70">39.50%</text>
        <text x="30" y="82">39.00%</text><text x="30" y="94">38.50%</text><text x="30" y="106">38.00%</text>
      </g>
      <line x1="34" y1="104" x2="222" y2="104" stroke="#999" stroke-width=".6"/>
      <line x1="34" y1="8" x2="34" y2="104" stroke="#999" stroke-width=".6"/>
      <polygon points="38,14 214,80 214,104 38,104" fill="#3a95d6"/>
      <g font-size="5.5" fill="#555" font-family="Open Sans, sans-serif" text-anchor="middle">
        <text x="40" y="114">FY13</text><text x="126" y="114">FY14</text><text x="212" y="114">FY15</text>
      </g>
    </svg>

    <h2 class="section-heading" style="left:26px; top:372px;">Warehouse owners have a challenge to exit their business</h2>

    <div class="exit-row" style="top:402px; height:40px;">
      <div class="exit-row__panel"></div>
      <div class="exit-row__label"><strong>Glut of sellers</strong> Many warehouse owners are aging</div>
      <ul class="tick-list" style="color:var(--blue)">
        <li><svg><use href="#tick"/></svg>The first “baby boomer” owners turn 69 in 2015 and are within reach of retirement</li>
      </ul>
    </div>

    <div class="exit-row" style="top:450px; height:120px;">
      <div class="exit-row__panel"></div>
      <div class="exit-row__label"><strong>Inability to attract buyers</strong><br>Owners have limited ability to sell</div>
      <ul class="tick-list" style="color:var(--blue)">
        <li><svg><use href="#tick"/></svg>Many single-site operators lack the size and scale to attract a corporate buyer</li>
        <li><svg><use href="#tick"/></svg>Succession through the family is often not an option e.g. no interest from next generation to take on the business risk</li>
        <li><svg><use href="#tick"/></svg>Many businesses difficult to sell due to dependence on owner operator</li>
        <li><svg><use href="#tick"/></svg>Low EBIT would not attract financial buyers</li>
      </ul>
    </div>

    <div class="exit-row" style="top:590px; height:76px;">
      <div class="exit-row__panel"></div>
      <div class="exit-row__label" style="top:14px;"><strong>Need to cash-out</strong> Yet many owners have genuine need to sell</div>
      <ul class="tick-list" style="color:var(--blue)">
        <li><svg><use href="#tick"/></svg>Substantial capital costs that need to be recovered</li>
        <li><svg><use href="#tick"/></svg>Long-term leases with substantial penalties for early termination</li>
        <li><svg><use href="#tick"/></svg>Need to fund retirement</li>
      </ul>
    </div>
  </section>

  <!-- Right page: the solution -->
  <section class="page page--right">
    <svg class="hero-photo" viewBox="0 0 566 260" role="img" aria-label="Photograph of hanging light bulbs in blue light with one bulb glowing bright">
      <defs>
        <radialGradient id="photoGrad" cx=".75" cy=".45" r=".8">
          <stop offset="0" stop-color="#bfe2ff"/>
          <stop offset=".25" stop-color="#2d6bb0"/>
          <stop offset="1" stop-color="#0c2a55"/>
        </radialGradient>
      </defs>
      <path d="M0 0 H566 V250 C440 200 300 190 0 130 Z" fill="url(#photoGrad)"/>
    </svg>

    <h2 class="solution-title">The solution<br>(What?)</h2>
    <p class="solution-intro">Southern Linked Logistics provides a national platform to deliver scale to its members. Through this scale, SLL and its members will secure new business. The value of members’ businesses will increase, and members will be presented with multiple options to exit.</p>

    <h2 class="section-heading benefit-heading">SLL provides delivers scale, synergies, value &amp; potential exit to its membership</h2>

    <div class="benefits">
      <div class="benefit">
        <div class="benefit__band"></div>
        <div class="benefit__badge">Scale</div>
        <ul class="tick-list" style="color:#fff">
          <li><svg><use href="#tick"/></svg>By leveraging its membership and national presence, SLL will present as a premium logistics provider within the Australian market – a credible alternative to the large corporates</li>
          <li><svg><use href="#tick"/></svg>Initial scale at launch is intended to exceed 100,000m2 with over $50 million in annual turnover</li>
          <li><svg><use href="#tick"/></svg>SLL provides its members with a national network</li>
        </ul>
      </div>
      <div class="benefit">
        <div class="benefit__band"></div>
        <div class="benefit__badge">Synergy</div>
        <ul class="tick-list" style="color:#fff">
          <li><svg><use href="#tick"/></svg>SLL will provide a centralised business development function on behalf of its members</li>
          <li><svg><use href="#tick"/></svg>Where SLL can leverage its scale, it will provide reduce costs to its members</li>
        </ul>
      </div>
      <div class="benefit">
        <div class="benefit__band"></div>
        <div class="benefit__badge">Value</div>
        <ul class="tick-list" style="color:#fff">
          <li><svg><use href="#tick"/></svg>Members’ businesses will increase in value as new work is introduced &amp; customer base is diversified</li>
          <li><svg><use href="#tick"/></svg>With its scale, the ultimate sale of SLL will be at a higher multiple and value than any individual member could achieve</li>
        </ul>
      </div>
      <div class="benefit">
        <div class="benefit__band"></div>
        <div class="benefit__badge">Potential<br>Exit</div>
        <ul class="tick-list" style="color:#fff">
          <li><svg><use href="#tick"/></svg>For members who wish to sell some or all of their business, SLL will offer to acquire part of their business</li>
          <li><svg><use href="#tick"/></svg>This initial exit will enable owners to “take some cash off the table” and de-risk</li>
        </ul>
      </div>
    </div>
  </section>
</main>
</body>
</html>
```